Velmar Radio Web

Radio Station web site to include but not limited:

- About US (company profile)
- Now playing (from our streaming server link)
- Upcoming events with a possibility to have photos for advertisement purpose, etc...
- Language switch from Russian to English

- Member section:
Login module (with new user name and password, forgot password, etc...)
Login module with Chatterloop details
Request a song
LIKE feature with Chatterloop...

- Social links: (along with Chatterloop LIKE)
Send page to a friend
share / chatterloop share
Chat section where all logged users can chat in the same room.

- Contact us (Radio email ID )
- iPAD - iPOD compatible

2 Websites were found to match the design that we re looking for:
http://www.trenivak.com and
http://carlosmendrutt.com

The site colors shall be matching and ongoing with our logo colors and designs as well.

Thanks,
Velmar Radio Team
Updates

Extended dead line and project is guaranteed.

Project Deadline Extended
Reason: Need more designs for review...

Industry/Entity Type

Radio

Requirements
Must have
• Chatterloop Login
Chatterloop LIKE
Users Chat Section
Language Switch
iPAD - iPOD compatible
Nice to have
• Less pages switch. Initial shall be to switch from russian to english (or EN to RU) but the less pages we flip, the better. (except pop ups for log in, request a song, etc...)

```html
<!DOCTYPE html>
<html lang="en">
<head>
<meta charset="utf-8">
<title>Velmar Radio</title>
<link href="https://fonts.googleapis.com/css2?family=Arimo:wght@400;700&family=Tinos&display=swap" rel="stylesheet">
<style>
:root{
  --navy:#0d3a78;
  --navy-dark:#1a2560;
  --blue-title:#0b3a7a;
  --link:#1c3d7a;
  --gold:#e4b400;
  --gold-light:#f7d64a;
  --gold-edge:#b98f00;
  --text:#333;
  --grey-panel:#e9e9e9;
  --white:#fff;
  --footer-top:#1e5aa0;
  --footer-bottom:#0b3b7c;
}
*{box-sizing:border-box;margin:0;padding:0}
html,body{width:1026px;height:1200px;overflow:hidden;background:#fff}
body{position:relative;font-family:"Arimo",Arial,sans-serif;color:var(--text)}
.abs{position:absolute}

/* top strip */
.top-bar{left:33px;top:0;width:970px;height:49px;border-radius:0 0 6px 6px;background:linear-gradient(#fff,#dcdcdc)}
.lang-label{left:51px;top:19px;font-size:13px;color:#222}
.flag{top:20px;width:23px;height:15px}
.live-chat{left:535px;top:0;width:200px;height:46px;background:linear-gradient(#fff,#e4e4e4);border-radius:0 0 4px 4px}
.live-chat .dot{position:absolute;left:22px;top:8px;width:30px;height:30px;border-radius:50%;background:#3b6fc4}
.live-chat span{position:absolute;left:74px;top:14px;font-size:14px;color:var(--link)}
.social{top:10px;width:28px;height:28px;border-radius:50%;background:#9aa7b8}
.navy-rule{left:0;top:51px;width:1026px;height:9px;background:var(--navy-dark)}

/* header */
.header-band{left:0;top:62px;width:1026px;height:164px;background:linear-gradient(#f3f3f3,#cfcfcf)}
.track{left:113px;top:72px;width:814px;height:10px;border-radius:5px;background:#f4f4f4;box-shadow:inset 0 0 0 1px #ccc}
.track .seg{position:absolute;top:0;height:10px;border-radius:5px;background:#222}
.logo-panel{left:111px;top:90px;width:563px;height:122px;border-radius:5px;background:linear-gradient(#fbfbfb,#e3e3e3)}
.logo-dot{left:134px;top:96px;width:112px;height:112px;border-radius:50%;background:var(--navy)}
.brand{left:270px;top:132px;font-family:"Tinos",serif;font-size:39px;color:var(--blue-title);letter-spacing:1px}
.eq{left:694px;top:92px;width:219px;height:98px;border-radius:6px;background:linear-gradient(#f7f7f7,#cfcfcf)}
.transport{left:731px;top:196px;width:161px;height:22px;border-radius:3px;background:linear-gradient(#fff,#c8c8c8);box-shadow:0 0 0 1px #999}

/* nav */
.nav{left:34px;top:228px;width:969px;height:49px;background:linear-gradient(#fff,#dedede);display:flex;align-items:center;font-size:14px;color:var(--link)}
.nav a{color:var(--link);text-decoration:none}
.nav .sep{margin:0 10px;color:#333}
.btn-gold{display:inline-flex;align-items:center;justify-content:center;background:linear-gradient(var(--gold-light),var(--gold));border:1px solid var(--gold-edge);border-radius:6px;color:#222;font-size:14px}
.nav .home{width:88px;height:33px;margin:0 22px 0 36px}

/* side boxes */
.side-box{left:22px;width:243px;border-radius:5px;background:var(--navy);padding:7px}
.side-inner{width:100%;height:100%;border-radius:5px;background:linear-gradient(#fafafa,#c9c9c9);position:relative}
.box-title{position:absolute;left:21px;top:2px;width:183px;height:42px;border-radius:0 0 5px 5px;background:linear-gradient(#fff,#dcdcdc);display:flex;align-items:center;justify-content:center;font-size:19px;color:var(--blue-title);box-shadow:0 1px 2px rgba(0,0,0,.3)}
.field-label{position:absolute;left:14px;font-size:12.5px;color:#222}
.field{position:absolute;left:92px;width:110px;height:26px;background:#fff;border:1px solid #ccc;border-radius:3px}
.forgot{position:absolute;left:109px;top:128px;font-size:11px;color:#222}
.event{position:absolute;left:5px;height:64px;width:220px}
.event .thumb{position:absolute;left:0;top:0;width:63px;height:63px;border:1px solid #999;background:linear-gradient(#8e8e8e,#3a3a3a)}
.event p{position:absolute;left:67px;top:-1px;font-size:12.5px;line-height:20.5px;color:#444}
.view-more{position:absolute;left:137px;top:302px;font-size:12px;color:var(--link)}

/* main */
.slider{left:284px;top:298px;width:726px;height:345px;border-radius:5px;background:var(--navy);padding:6px}
.slider .photo{width:100%;height:100%;background:linear-gradient(180deg,#8f7d70,#cbb9a8 40%,#5a4c45)}
.arrow{top:448px;width:26px;height:50px;background:#222;border-radius:4px;color:#fff;font-size:13px;display:flex;align-items:center;justify-content:center}
.now{left:301px;top:661px;width:266px;height:193px;background:linear-gradient(135deg,#e05a63,#f3a2a0)}
.now-title{left:301px;top:676px;width:266px;text-align:center;font-size:23px;color:#222}
.player{left:301px;top:855px;width:266px;height:38px;background:linear-gradient(#eef3fa,#b8c7da);border:1px solid #9fb0c7}
.divider{left:622px;top:675px;height:190px;border-left:1px dotted #666}
.chat-title{left:732px;top:674px;font-size:18px;color:var(--blue-title)}
.chat-photo{left:671px;top:714px;width:156px;height:112px;border:1px solid #999;background:linear-gradient(#f2f2f2,#b7423f 55%,#2a2a2a)}
.chat-text{left:839px;top:716px;width:160px;font-size:12px;line-height:20.5px;color:#333}
.chat-btn{left:847px;top:817px;width:130px;height:34px}

/* footer */
.footer{left:0;top:904px;width:1026px;height:243px;background:linear-gradient(var(--footer-top),var(--footer-bottom))}
.foot-title{top:932px;width:204px;height:43px;border-radius:3px;background:linear-gradient(#fff,#dcdcdc);display:flex;align-items:center;justify-content:center;font-size:19px;color:var(--blue-title)}
.foot-text{color:#fff;font-size:12px;line-height:18.5px}
.foot-btn{width:129px;height:33px}
.legal{left:0;top:1157px;width:1026px;text-align:center;font-size:12.5px;color:#222}
.legal .sep{margin:0 16px}
.copyright{left:0;top:1181px;width:1026px;text-align:center;font-size:12.5px;color:#222}
</style>
</head>
<body>

<div class="abs top-bar"></div>
<div class="abs lang-label">Language :</div>
<svg class="abs flag" style="left:125px" viewBox="0 0 60 36" aria-label="English">
  <rect width="60" height="36" fill="#012169"/>
  <path d="M0 0L60 36M60 0L0 36" stroke="#fff" stroke-width="7"/>
  <path d="M0 0L60 36M60 0L0 36" stroke="#c8102e" stroke-width="2.5"/>
  <path d="M30 0V36M0 18H60" stroke="#fff" stroke-width="11"/>
  <path d="M30 0V36M0 18H60" stroke="#c8102e" stroke-width="6"/>
</svg>
<svg class="abs flag" style="left:163px" viewBox="0 0 60 36" aria-label="Russian">
  <rect width="60" height="12" fill="#fff"/>
  <rect y="12" width="60" height="12" fill="#0039a6"/>
  <rect y="24" width="60" height="12" fill="#d52b1e"/>
</svg>
<div class="abs live-chat"><div class="dot"></div><span>Live Chat</span></div>
<div class="abs social" style="left:836px" aria-label="Chatterloop"></div>
<div class="abs social" style="left:881px" aria-label="Microblog"></div>
<div class="abs social" style="left:925px" aria-label="News feed"></div>
<div class="abs social" style="left:968px" aria-label="Video channel"></div>
<div class="abs navy-rule"></div>

<div class="abs header-band"></div>
<div class="abs track">
  <div class="seg" style="left:0;width:52px"></div>
  <div class="seg" style="left:286px;width:255px"></div>
  <div class="seg" style="left:758px;width:56px"></div>
</div>
<div class="abs logo-panel"></div>
<div class="abs logo-dot"></div>
<div class="abs brand">VELMAR RADIO</div>

<svg class="abs eq" viewBox="0 0 219 98" aria-label="Equalizer">
  <rect x="10" y="6" width="2" height="70" fill="#888"/>
  <rect x="5" y="32" width="12" height="16" rx="2" fill="#eee" stroke="#777"/>
  <rect x="3" y="78" width="24" height="9" rx="4" fill="#3a8a1e"/>
  <text x="15" y="85.5" font-size="7" fill="#fff" text-anchor="middle" font-family="Arimo,sans-serif">VOL</text>
  <rect x="41" y="8" width="20" height="78" rx="4" fill="#111"/>
  <g font-size="8" fill="#6d8" text-anchor="middle" font-family="Arimo,sans-serif">
    <text x="51" y="22">3</text><text x="51" y="41">0</text><text x="51" y="60">-6</text><text x="51" y="79">-12</text>
  </g>
  <g fill="#eee" stroke="#777">
    <rect x="76" y="52" width="12" height="14" rx="2"/><rect x="104" y="52" width="12" height="14" rx="2"/>
    <rect x="132" y="52" width="12" height="14" rx="2"/><rect x="160" y="52" width="12" height="14" rx="2"/>
    <rect x="188" y="52" width="12" height="14" rx="2"/>
  </g>
  <g fill="#888"><rect x="81" y="6" width="2" height="72"/><rect x="109" y="6" width="2" height="72"/><rect x="137" y="6" width="2" height="72"/><rect x="165" y="6" width="2" height="72"/><rect x="193" y="6" width="2" height="72"/></g>
  <g fill="#111"><rect x="72" y="78" width="22" height="9" rx="4"/><rect x="100" y="78" width="22" height="9" rx="4"/><rect x="128" y="78" width="22" height="9" rx="4"/><rect x="156" y="78" width="22" height="9" rx="4"/><rect x="184" y="78" width="22" height="9" rx="4"/></g>
  <g font-size="7" fill="#fff" text-anchor="middle" font-family="Arimo,sans-serif">
    <text x="83" y="85.5">300</text><text x="111" y="85.5">600</text><text x="139" y="85.5">1K</text><text x="167" y="85.5">8K</text><text x="195" y="85.5">16K</text>
  </g>
</svg>
<svg class="abs transport" viewBox="0 0 161 22" aria-label="Playback controls">
  <g stroke="#999"><path d="M40 3V19M80 3V19M120 3V19"/></g>
  <g fill="#333">
    <path d="M15 11l5-4v8zM20 11l5-4v8z"/><path d="M57 7l7 4-7 4z"/>
    <path d="M93 7l5 4-5 4zM98 7l5 4-5 4z"/><rect x="136" y="7" width="8" height="8"/>
  </g>
</svg>

<nav class="abs nav">
  <span class="btn-gold home">Home</span>
  <a>Products</a><span class="sep">|</span>
  <a>Download</a><span class="sep">|</span>
  <a>Services</a><span class="sep">|</span>
  <a>Testimonials</a><span class="sep">|</span>
  <a>FAQ</a><span class="sep">|</span>
  <a>Links</a><span class="sep">|</span>
  <a>Chatterloop Login</a><span class="sep">|</span>
  <a>Contact</a>
</nav>

<section class="abs side-box" style="top:294px;height:222px">
  <div class="side-inner">
    <div class="box-title">Login</div>
    <span class="field-label" style="top:57px">User Name :</span>
    <span class="field" style="top:54px"></span>
    <span class="field-label" style="top:101px">Password &nbsp;:</span>
    <span class="field" style="top:95px"></span>
    <span class="forgot">Forgot Password</span>
    <span class="btn-gold" style="position:absolute;left:101px;top:157px;width:89px;height:33px">Submit</span>
  </div>
</section>

<section class="abs side-box" style="top:531px;height:355px">
  <div class="side-inner">
    <div class="box-title">Upcoming Events</div>
    <div class="event" style="top:69px"><div class="thumb" role="img" aria-label="Event promo photo of a DJ"></div><p>SECURE EXHIBITION<br>19 Sep, 2011 (10:00 AM<br>ORVEN GROUNDS.</p></div>
    <div class="event" style="top:152px"><div class="thumb" role="img" aria-label="Event promo photo of a microphone"></div><p>SECURE EXHIBITION<br>19 Sep, 2011 (10:00 AM<br>ORVEN GROUNDS.</p></div>
    <div class="event" style="top:235px"><div class="thumb" role="img" aria-label="Event promo photo of a studio microphone" style="background:linear-gradient(#eee,#999)"></div><p style="left:71px">SECURE EXHIBITION<br>19 Sep, 2011 (10:00 AM<br>ORVEN GROUNDS.</p></div>
    <span class="view-more">View More</span>
  </div>
</section>

<div class="abs slider"><div class="photo" role="img" aria-label="Photo of a group laughing while reading scripts in a studio lounge"></div></div>
<div class="abs arrow" style="left:290px">&lt;</div>
<div class="abs arrow" style="left:980px">&gt;</div>

<div class="abs now" role="img" aria-label="Photo of a smiling listener wearing headphones"></div>
<div class="abs now-title">Now Playing</div>
<svg class="abs player" viewBox="0 0 266 38" aria-label="Audio player">
  <rect x="8" y="4" width="240" height="7" rx="3" fill="#fff" stroke="#99a"/>
  <rect x="10" y="5" width="18" height="5" rx="2" fill="#4c4"/>
  <g fill="#fff" stroke="#556"><circle cx="24" cy="26" r="8"/><circle cx="47" cy="26" r="6"/><circle cx="77" cy="26" r="6"/><circle cx="97" cy="26" r="6"/><circle cx="117" cy="26" r="6"/><circle cx="137" cy="26" r="6"/><circle cx="202" cy="26" r="6"/></g>
  <path d="M21 22l7 4-7 4z" fill="#223"/><rect x="44" y="23" width="6" height="6" fill="#223"/>
  <path d="M212 30L250 22V30z" fill="#4c4"/>
</svg>

<div class="abs divider"></div>
<h2 class="abs chat-title" style="font-weight:400">Chat Room</h2>
<div class="abs chat-photo" role="img" aria-label="Photo of three smiling businesswomen"></div>
<p class="abs chat-text">Lorem ipsum dolor sit amet, consectetuer adipiscing elit. Nam nibh. Nunc varius facilisis eros. Sed erat.</p>
<span class="abs btn-gold chat-btn">Go to Chat Room</span>

<footer class="abs footer"></footer>
<div class="abs foot-title" style="left:59px">Request a Song</div>
<p class="abs foot-text" style="left:91px;top:988px;font-weight:700">Korva FM<br>Tags: AC<br>Site: http://www.korva.fm<br>Recently Played: Mira<br>Santell &amp; Dex Harlow</p>
<span class="abs btn-gold foot-btn" style="left:91px;top:1097px">Click here</span>

<div class="abs foot-title" style="left:378px">Send Page to Friend</div>
<p class="abs foot-text" style="left:396px;top:993px;line-height:14.5px">Loreum Ipsum Dollar, sit amet.<br>Loreum Ipsum Dollar, sit amet.</p>
<p class="abs foot-text" style="left:396px;top:1040px;line-height:14.5px">Loreum Ipsum Dollar, sit amet.<br>Loreum Ipsum Dollar, sit amet.</p>
<span class="abs btn-gold foot-btn" style="left:414px;top:1097px">Click here</span>

<div class="abs foot-title" style="left:738px">CONTACT ME</div>
<span class="abs foot-text" style="left:750px;top:1005px;font-size:14px">Address &nbsp;:</span>
<p class="abs foot-text" style="left:836px;top:1010px;line-height:20.5px">Lorem ipsum dolor sit amet,<br>consectetuer adipiscing elit.</p>
<span class="abs foot-text" style="left:775px;top:1075px">Phone : &nbsp;021 4870 1152</span>
<span class="abs foot-text" style="left:775px;top:1114px">Email : velmarradio@velmarmail.com</span>

<div class="abs legal">Privacy Policy<span class="sep">|</span>Terms &amp; Conditions<span class="sep">|</span>Contact Us</div>
<div class="abs copyright">Copyright © velmarradio, All Rights Reserved</div>

</body>
</html>
```